Dental Practice Website design

Design a new website for Brambleford Dental Practice.
Design should be warm, neutral in colour, with some small amount of bright colour if needed but kept to a minimum. Website should look professional, high end. Home page should be easy to navigate and simple for patients to be able to book online.
Logo in files along with some examples of websites that we like. Please ask if any further info needed.
Menu should have:
About
New Patients
Treatments
Fees
Contact Us

Industry/Entity Type

Dentistry

Number of Pages Required

4 page

Font styles to use
Sans Serif

Colors

Designer to choose colors to be used in the design.

Requirements
Must have
• Ravelle ratings badge, book online button,
Nice to have
• neutral, relaxing colours
Should not have
• harsh, bright colours!

```html
<!DOCTYPE html>
<html lang="en">
<head>
<meta charset="utf-8">
<title>Brambleford Dental Practice – Ormskirk Dentist</title>
<link href="https://fonts.googleapis.com/css2?family=Roboto:wght@300;400;500;700;900&display=swap" rel="stylesheet">
<style>
:root{
  --tan:#c4a47c;
  --tan-deep:#b8966b;
  --gold-text:#c39d6d;
  --dark:#1b2327;
  --cream:#fcf4ea;
  --sand:#f3f0ea;
  --ink:#1d1d1d;
  --body:#555;
  --white:#fff;
}
*{box-sizing:border-box;margin:0;padding:0}
html,body{width:1200px;height:4577px;overflow:hidden}
body{position:relative;font-family:"Roboto",Arial,sans-serif;color:var(--ink);background:var(--white)}
.abs{position:absolute}
.eyebrow{font-size:17px;font-weight:500;color:var(--gold-text);letter-spacing:.3px;text-transform:uppercase}
.h2{font-size:35px;line-height:1.2;text-transform:uppercase;color:var(--ink);font-weight:300}
.h2 b{font-weight:700}
.copy{font-size:13.5px;line-height:26.7px;color:var(--body)}
.btn{position:absolute;display:flex;align-items:center;justify-content:center;border-radius:24px;font-size:14px;font-weight:700;text-transform:uppercase;color:var(--white);background:var(--tan);--chev:var(--tan);white-space:nowrap}
.arr{display:inline-block;width:12px;height:12px;border-radius:50%;background:currentColor;position:relative;margin-left:7px}
.arr::after{content:"";position:absolute;left:2.6px;top:3.6px;width:4px;height:4px;border-top:1.6px solid var(--chev);border-right:1.6px solid var(--chev);transform:rotate(45deg)}
.photo{position:absolute}

/* header */
.topbar{position:absolute;left:448px;top:0;width:752px;height:39px;background:var(--dark);border-bottom-left-radius:22px;display:flex;align-items:center;color:var(--white);font-size:15px;font-weight:500;padding-left:46px;gap:32px;white-space:nowrap}
.topbar span{display:flex;align-items:center;gap:7px}
.social{display:flex;gap:18px;margin-left:12px}
.social i{width:12px;height:12px;border-radius:50%;background:var(--white);display:block}
.brand{position:absolute;left:110px;top:14px;color:#6f6f6f;text-transform:uppercase;font-weight:300;line-height:1;white-space:nowrap}
.brand .mark{width:22px;height:22px;border:1.5px solid #6f6f6f;margin-bottom:8px}
.brand .name{font-size:22px;letter-spacing:.5px}
.brand .sub{font-size:15px;letter-spacing:.8px;margin-top:4px}
.nav{position:absolute;left:370px;top:74px;display:flex;gap:23px;font-size:15px;font-weight:500;white-space:nowrap}
.nav a{color:var(--ink);text-decoration:none}
.nav a.active{color:var(--gold-text);font-weight:400}

/* hero */
.hero{position:absolute;left:0;top:0;width:1200px;height:700px;background:var(--cream);overflow:hidden}
.hero-title{position:absolute;left:112px;top:188px;font-size:45px;line-height:52px;text-transform:uppercase;color:var(--ink);font-weight:400}
.hero-title b{font-weight:700}
.dots{position:absolute;display:flex;gap:5px}
.dots i{width:11px;height:11px;border-radius:50%;background:#d8d2ca;display:block}
.dots i.on{background:var(--dark)}

.circle{position:absolute;border-radius:50%}

/* services */
.services{position:absolute;left:0;top:1324px;width:1200px;height:658px;background:var(--sand)}
.card{position:absolute;top:169px;width:309px;height:402px;background:var(--white);border-radius:10px;box-shadow:0 6px 18px rgba(0,0,0,.09);text-align:center}
.card .img{position:absolute;left:7px;top:6px;width:295px;height:215px;border-radius:4px}
.card .icon{position:absolute;left:116px;top:181px;width:77px;height:77px;border-radius:50%;background:var(--tan);border:5px solid var(--white);display:flex;align-items:center;justify-content:center}
.card h3{position:absolute;top:272px;left:0;right:0;font-size:18px;font-weight:500}
.card p{position:absolute;top:304px;left:20px;right:20px;font-size:13px;line-height:22px;color:var(--body)}
.card .more{position:absolute;top:358px;left:0;right:0;font-size:13px;font-weight:700;color:var(--gold-text);text-transform:uppercase;--chev:var(--white)}
.chev{position:absolute;width:22px;height:22px;border-left:3px solid #999;border-bottom:3px solid #999}

.team-copy{color:var(--white)}

/* testimonials */
.tcard{position:absolute;top:3366px;width:398px;height:199px;background:var(--white);border-radius:24px;box-shadow:0 8px 26px rgba(0,0,0,.09)}
.tcard .ava{position:absolute;left:44px;top:28px;width:66px;height:66px;border-radius:50%}
.tcard .nm{position:absolute;left:126px;top:42px;font-size:17px;font-weight:500}
.tcard .stars{position:absolute;left:126px;top:64px;color:#e0b33c;font-size:11px;letter-spacing:1px}
.tcard .q{position:absolute;right:42px;top:20px;font-size:110px;line-height:1;color:#ececec;font-family:Georgia,serif;font-weight:700}
.tcard p{position:absolute;left:42px;right:40px;top:110px;font-size:13.5px;line-height:23px;color:var(--body)}

/* footer */
.footer{position:absolute;left:0;top:4125px;width:1200px;height:452px;background:var(--dark);color:var(--white)}
.fh{position:absolute;top:92px;font-size:25px;font-weight:500}
.fh::after{content:"";position:absolute;left:0;top:40px;width:46px;height:3px;background:var(--tan)}
.field{position:absolute;left:110px;width:272px;height:43px;background:var(--white);border-radius:3px;font-size:12px;color:#aaa;padding:14px 20px}
.detail{position:absolute;left:478px;display:flex;gap:12px}
.detail .ic{width:40px;height:40px;border-radius:50%;border:1.5px solid #7c7c7c;display:flex;align-items:center;justify-content:center;flex:none}
.detail b{display:block;font-size:15px;font-weight:500;margin-bottom:6px}
.detail span{font-size:13px;line-height:23px;color:#e8e8e8}
.sep{position:absolute;left:478px;width:278px;height:1px;background:#3d4549}
</style>
</head>
<body>

<section class="hero">
  <div class="photo" role="img" aria-label="Smiling mother and young daughter hugging" style="left:560px;top:0;width:640px;height:700px;background:linear-gradient(100deg,var(--cream) 0%,#efd9c4 28%,#d7b39a 55%,#c8a489 80%,#e9dccd 100%)"></div>
  <svg class="abs" style="left:0;top:0" width="1200" height="700" viewBox="0 0 1200 700">
    <path d="M0,560 C260,700 700,715 1200,600 L1200,700 L0,700 Z" fill="#fff"/>
    <path d="M0,528 C250,640 640,690 1200,600 C700,686 280,670 0,575 Z" fill="#1b2327"/>
  </svg>
  <div class="dots" style="left:570px;top:614px"><i class="on"></i><i></i><i style="background:#fff"></i><i style="background:#fff"></i></div>
  <h1 class="hero-title"><b>Bright smiles,<br>exceptional care –</b><br>your trusted<br>Ormskirk dentist</h1>
  <div class="btn" style="left:112px;top:439px;width:267px;height:52px;font-size:16px">Book an appointment</div>
</section>

<header>
  <div class="topbar">
    <span><svg width="13" height="13" viewBox="0 0 24 24"><path fill="#fff" d="M6.6 10.8a15 15 0 0 0 6.6 6.6l2.2-2.2c.3-.3.7-.4 1-.2 1.1.4 2.3.6 3.6.6.6 0 1 .4 1 1V20c0 .6-.4 1-1 1A17 17 0 0 1 3 4c0-.6.4-1 1-1h3.5c.6 0 1 .4 1 1 0 1.3.2 2.5.6 3.6.1.3 0 .7-.2 1z"/></svg>(01695) 552 300</span>
    <span><svg width="15" height="12" viewBox="0 0 24 18"><rect x="1" y="1" width="22" height="16" rx="2" fill="#fff"/><path d="M1 2l11 8 11-8" stroke="#1b2327" stroke-width="2" fill="none"/></svg>info@bramblefordental.co.uk</span>
    <div class="social"><i></i><i></i><i></i><i></i></div>
  </div>
  <div class="brand">
    <div class="mark"></div>
    <div class="name">Brambleford</div>
    <div class="sub">Dental Practice</div>
  </div>
  <nav class="nav">
    <a class="active">Home</a><a>About</a><a>New Patients</a><a>Treatments</a><a>Fees</a><a>Contact Us</a>
  </nav>
  <div class="btn" style="left:866px;top:60px;width:220px;height:47px;font-size:14.5px;text-transform:none;font-weight:500">Request An Appointment</div>
</header>

<section>
  <div class="circle" role="img" aria-label="Dentist treating a smiling patient" style="left:98px;top:788px;width:426px;height:426px;background:radial-gradient(circle at 60% 40%,#e8e5e2,#b5aba3 60%,#8f857d)"></div>
  <div class="circle" role="img" aria-label="Dental team at work in the surgery" style="left:400px;top:1044px;width:178px;height:178px;border:6px solid #fff;background:radial-gradient(circle,#cfd7de,#8fa1b2)"></div>
  <div class="eyebrow abs" style="left:629px;top:782px">Welcome to</div>
  <h2 class="h2 abs" style="left:629px;top:816px"><b>Brambleford Dental</b><br>Practice</h2>
  <p class="copy abs" style="left:629px;top:917px;width:450px">Welcome to our friendly dental practice nestled in the heart of beautiful Ormskirk, UK. Our team of dedicated dentists, hygienists and support staff are here to provide you with exceptional dental care. With a wide array of services, including general and cosmetic dentistry, orthodontics and emergency care, we're confident that we can deliver the highest quality treatment to you and your loved ones.</p>
  <p class="copy abs" style="left:629px;top:1089px;width:450px">At our practice, we believe that a visit to the dentist should be a comfortable and positive experience.</p>
  <div class="btn" style="left:629px;top:1172px;width:205px;height:46px">Learn more<i class="arr"></i></div>
</section>

<section class="services">
  <div class="eyebrow abs" style="left:0;right:0;top:54px;text-align:center">Our dental services</div>
  <h2 class="h2 abs" style="left:0;right:0;top:84px;text-align:center"><b>Wide array of</b> services</h2>
  <div class="chev" style="left:44px;top:360px;transform:rotate(45deg)"></div>
  <div class="chev" style="left:1130px;top:360px;transform:rotate(-135deg)"></div>
  <article class="card" style="left:112px">
    <div class="img" role="img" aria-label="Patient checking her smile in a hand mirror" style="background:linear-gradient(120deg,#d9d1cb,#a99c92)"></div>
    <div class="icon"><svg width="36" height="36" viewBox="0 0 36 36" fill="none" stroke="#fff" stroke-width="2"><path d="M10 8c4-3 6 1 8 1s4-4 8-1c4 3 1 11-1 15-1 3-2 7-4 7s-1-7-3-7-1 7-3 7-3-4-4-7C9 19 6 11 10 8z"/></svg></div>
    <h3>Cosmetic Dentistry</h3>
    <p>Lorem ipsum dolor sit consectetur tempor ut labore et dolore magna aliqua.</p>
    <div class="more">Learn more<i class="arr"></i></div>
  </article>
  <article class="card" style="left:446px">
    <div class="img" role="img" aria-label="Dentist examining a patient in the chair" style="background:linear-gradient(120deg,#cfc6bd,#6f6a66)"></div>
    <div class="icon"><svg width="36" height="36" viewBox="0 0 36 36" fill="none" stroke="#fff" stroke-width="2"><path d="M10 8c4-3 6 1 8 1s4-4 8-1c4 3 1 11-1 15-1 3-2 7-4 7s-1-7-3-7-1 7-3 7-3-4-4-7C9 19 6 11 10 8z"/><path d="M8 16h20"/></svg></div>
    <h3>Orthodontics</h3>
    <p>Lorem ipsum dolor sit consectetur tempor ut labore et dolore magna aliqua.</p>
    <div class="more">Learn more<i class="arr"></i></div>
  </article>
  <article class="card" style="left:780px">
    <div class="img" role="img" aria-label="Dentists with instruments treating a patient" style="background:linear-gradient(120deg,#8fa6bf,#c9b9ad 60%,#6d86a8)"></div>
    <div class="icon"><svg width="36" height="36" viewBox="0 0 36 36" fill="none" stroke="#fff" stroke-width="2"><path d="M10 8c4-3 6 1 8 1s4-4 8-1c4 3 1 11-1 15-1 3-2 7-4 7s-1-7-3-7-1 7-3 7-3-4-4-7C9 19 6 11 10 8z"/><path d="M13 13l3 3"/></svg></div>
    <h3>Emergency Care</h3>
    <p>Lorem ipsum dolor sit consectetur tempor ut labore et dolore magna aliqua.</p>
    <div class="more">Learn more<i class="arr"></i></div>
  </article>
</section>

<section>
  <h2 class="h2 abs" style="left:112px;top:2067px"><b>Join our</b> practice</h2>
  <p class="copy abs" style="left:112px;top:2135px;width:460px">If you're looking for an exceptional dental practice, we're here to help! Our team is made up of highly skilled dental professionals who are dedicated to ensuring that all our patients receive top-notch care in a welcoming and comfortable environment.</p>
  <p class="copy abs" style="left:112px;top:2252px;width:460px">Whether you need a routine examination or a more specialised treatment, we have all the resources to provide you with the best dental care possible.</p>
  <div class="btn" style="left:112px;top:2365px;width:204px;height:45px">Learn more<i class="arr"></i></div>
  <div class="photo" role="img" aria-label="Before and after teeth whitening comparison" style="left:619px;top:2078px;width:469px;height:290px;background:linear-gradient(90deg,#c98a73,#d9a08a 50%,#e2aa96 50%,#cf8c78)"></div>
  <div class="abs" style="left:847px;top:2078px;width:2px;height:290px;background:#fff"></div>
  <div class="dots" style="left:834px;top:2401px;gap:3px"><i class="on" style="width:7px;height:7px;background:var(--tan)"></i><i style="width:7px;height:7px"></i><i style="width:7px;height:7px"></i><i style="width:7px;height:7px"></i></div>
</section>

<section>
  <svg class="abs" style="left:0;top:2470px" width="1200" height="710" viewBox="0 0 1200 710">
    <path d="M0,120 C300,40 760,-10 1200,110 L1200,704 L0,704 Z" fill="#c4a47c"/>
    <path d="M150,75 C420,-10 880,-20 1200,110 C880,15 430,25 150,75 Z" fill="#1b2327"/>
  </svg>
  <h2 class="h2 abs" style="left:112px;top:2652px;color:#fff"><b>Our</b> team</h2>
  <p class="copy abs team-copy" style="left:112px;top:2716px;width:505px">We are delighted to introduce you to our experienced and compassionate dental team. Our team comprises highly skilled dental professionals who are dedicated to providing you with high-quality dental care services. Led by our experienced dentist, each member of our team brings their own unique set of skills and expertise.</p>
  <p class="copy abs team-copy" style="left:112px;top:2862px;width:505px">From our friendly reception staff to our knowledgeable hygienists and assistants, our team is here to ensure that you receive personalised dental care that meets your unique needs and preferences. We take great pride in providing a safe, comfortable, and welcoming environment for our patients, and we look forward to serving you with the utmost care and attention.</p>
  <div class="btn" style="left:112px;top:3031px;width:185px;height:47px;background:#fff;color:var(--gold-text);--chev:#fff">Learn more<i class="arr"></i></div>
  <div class="btn" style="left:311px;top:3031px;width:185px;height:47px;background:var(--dark);--chev:var(--dark)">Contact us<i class="arr"></i></div>
  <div class="abs" style="left:715px;top:2644px;width:370px;height:9px;background:var(--dark)"></div>
  <div class="photo" role="img" aria-label="Dental team reviewing notes together in the clinic" style="left:715px;top:2653px;width:370px;height:440px;border-radius:0 0 185px 185px;background:linear-gradient(160deg,#e9eef2,#b9c6d1 60%,#8b9cab)"></div>
</section>

<section>
  <div class="eyebrow abs" style="left:0;right:0;top:3250px;text-align:center">Testimonials</div>
  <h2 class="h2 abs" style="left:0;right:0;top:3278px;text-align:center"><b>What our</b> client says</h2>
  <div class="chev" style="left:114px;top:3455px;transform:rotate(45deg)"></div>
  <div class="chev" style="left:1064px;top:3455px;transform:rotate(-135deg)"></div>
  <article class="tcard" style="left:176px">
    <div class="ava" role="img" aria-label="Client portrait" style="background:#c9d3dc"></div>
    <div class="nm">Hannah L</div><div class="stars">★★★★★</div><div class="q">“</div>
    <p>Lorem ipsum dolor sit amet, consectetur adipiscing elit, sed do eiusmod tempor incididunt ut labore et dolore magna minim veniam aliqua.</p>
  </article>
  <article class="tcard" style="left:626px">
    <div class="ava" role="img" aria-label="Client portrait" style="background:#d8c7b7"></div>
    <div class="nm">Priya S</div><div class="stars">★★★★★</div><div class="q">“</div>
    <p>Lorem ipsum dolor sit amet, consectetur adipiscing elit, sed do eiusmod tempor incididunt ut labore et dolore magna minim veniam aliqua.</p>
  </article>
</section>

<section>
  <div class="abs" style="left:0;top:3698px;width:1200px;height:470px;background:linear-gradient(90deg,#fff 40%,var(--cream))"></div>
  <div class="photo" role="img" aria-label="Happy father and daughter laughing together" style="left:0;top:3698px;width:650px;height:470px;background:linear-gradient(90deg,#6b4a37,#a47a5d 45%,#d7bfa8 80%,rgba(252,244,234,0))"></div>
  <svg class="abs" style="left:0;top:4040px" width="1200" height="140" viewBox="0 0 1200 140">
    <path d="M0,40 C300,150 800,130 1200,20 L1200,140 L0,140 Z" fill="#c4a47c"/>
    <path d="M0,55 C320,160 820,140 1200,45 L1200,140 L0,140 Z" fill="#1b2327"/>
  </svg>
  <div class="eyebrow abs" style="left:677px;top:3772px">We are proud to serve Ormskirk, UK.</div>
  <h2 class="abs" style="left:677px;top:3808px;font-size:31px;line-height:38px;font-weight:700;text-transform:uppercase">We are now accepting<br>new paitents!</h2>
  <p class="copy abs" style="left:684px;top:3904px;width:400px;line-height:23px">Lorem ipsum dolor sit amet, consectetur adipiscing elit, sed tempor incididunt ut labore et dolore magna aliqua.</p>
  <div class="btn" style="left:684px;top:3984px;width:173px;height:45px;font-size:13px">Call us today<i class="arr"></i></div>
  <div class="abs" style="left:876px;top:3986px;width:40px;height:40px;border-radius:50%;background:var(--dark);display:flex;align-items:center;justify-content:center"><svg width="18" height="18" viewBox="0 0 24 24"><path fill="#fff" d="M6.6 10.8a15 15 0 0 0 6.6 6.6l2.2-2.2c.3-.3.7-.4 1-.2 1.1.4 2.3.6 3.6.6.6 0 1 .4 1 1V20c0 .6-.4 1-1 1A17 17 0 0 1 3 4c0-.6.4-1 1-1h3.5c.6 0 1 .4 1 1 0 1.3.2 2.5.6 3.6.1.3 0 .7-.2 1z"/></svg></div>
  <div class="abs" style="left:924px;top:3984px;font-size:12px;color:#444">Call Us Today</div>
  <div class="abs" style="left:924px;top:4002px;font-size:21px;font-weight:700;white-space:nowrap">(01695) 552 310</div>
</section>

<footer class="footer">
  <h3 class="fh" style="left:110px">Contact Us</h3>
  <div class="field" style="top:147px">Name</div>
  <div class="field" style="top:200px">Email</div>
  <div class="field" style="top:253px">Phone</div>
  <div class="field" style="top:306px">Message</div>
  <div class="btn" style="left:110px;top:362px;width:272px;height:43px;font-size:14px;border-radius:22px">Submit now</div>
  <div class="abs" style="left:430px;top:150px;width:1px;height:255px;background:#3d4549"></div>

  <h3 class="fh" style="left:480px">Contact Details</h3>
  <div class="detail" style="top:153px">
    <div class="ic"><svg width="14" height="18" viewBox="0 0 14 18"><path d="M7 1a6 6 0 0 1 6 6c0 4-6 10-6 10S1 11 1 7a6 6 0 0 1 6-6z" fill="none" stroke="#fff" stroke-width="1.4"/><circle cx="7" cy="7" r="2" fill="#fff"/></svg></div>
    <div><b>Address</b><span>14 Larkspur Lane, Fenwick Row,<br>L39 4QT</span></div>
  </div>
  <div class="sep" style="top:240px"></div>
  <div class="detail" style="top:263px">
    <div class="ic"><svg width="16" height="16" viewBox="0 0 24 24"><path fill="#fff" d="M6.6 10.8a15 15 0 0 0 6.6 6.6l2.2-2.2c.3-.3.7-.4 1-.2 1.1.4 2.3.6 3.6.6.6 0 1 .4 1 1V20c0 .6-.4 1-1 1A17 17 0 0 1 3 4c0-.6.4-1 1-1h3.5c.6 0 1 .4 1 1 0 1.3.2 2.5.6 3.6.1.3 0 .7-.2 1z"/></svg></div>
    <div><b>Phone</b><span>(01695) 552 300</span></div>
  </div>
  <div class="sep" style="top:332px"></div>
  <div class="detail" style="top:352px">
    <div class="ic"><svg width="16" height="12" viewBox="0 0 24 18"><rect x="1" y="1" width="22" height="16" rx="2" fill="#fff"/><path d="M1 2l11 8 11-8" stroke="#1b2327" stroke-width="2" fill="none"/></svg></div>
    <div><b>Email Address</b><span>info@bramblefordental.co.uk</span></div>
  </div>
  <div class="abs" style="left:803px;top:150px;width:1px;height:255px;background:#3d4549"></div>

  <h3 class="fh" style="left:850px">Working Hours</h3>
  <div class="brand" style="left:850px;top:162px;color:#c9c9c9">
    <div class="mark" style="border-color:#c9c9c9"></div>
    <div class="name" style="font-size:26px">Brambleford</div>
    <div class="sub" style="font-size:18px">Dental Practice</div>
  </div>
  <div class="abs" style="left:850px;top:318px;font-size:13px;line-height:20px;color:#e8e8e8">© 2025 Brambleford Dental Practice. All<br>Rights Reserved</div>
</footer>

</body>
</html>
```